design 3 a5 leaflets for tradesmen such as plumbers

I am looking for 3 flyers to be made for advertising painters and tradesmen. They are the type that have 10 - 12 tear away phone numbers.
I want 3 designs so that i can out compete the competition tolvane partner style. The winners will design 3 they don't need to be top class as the competition are generally home made. there will be three winners please use the phone numbers in the upload i gave you but advertise plumber on one leaflet and electrician saying local man ,competitive rates etc etc

```html
<!DOCTYPE html>
<html lang="en">
<head>
<meta charset="utf-8">
<title>Looking For Plumbers – Leaflet</title>
<link href="https://fonts.googleapis.com/css2?family=Arvo:wght@700&family=Open+Sans:wght@300;400;600;700;800&display=swap" rel="stylesheet">
<style>
  :root {
    --brand-blue: #1b9de2;
    --ink: #111111;
    --paper: #ffffff;
    --paper-soft: #f3f4f5;
    --frame: #dfe1e3;
    --dash: #8a8a8a;
  }
  * { box-sizing: border-box; margin: 0; padding: 0; }
  html, body { width: 859px; height: 1200px; overflow: hidden; background: var(--paper); }
  .leaflet {
    position: relative;
    width: 859px;
    height: 1200px;
    overflow: hidden;
    background: linear-gradient(var(--paper-soft), var(--paper) 40%);
    border: 14px solid var(--frame);
    font-family: "Open Sans", Arial, sans-serif;
    color: var(--ink);
  }
  .headline {
    position: absolute;
    top: 40px; left: 0; right: 0;
    text-align: center;
    white-space: nowrap;
    font-family: "Arvo", Georgia, serif;
    font-weight: 700;
    font-size: 92px;
    line-height: 1;
    color: var(--brand-blue);
  }
  .tool-art {
    position: absolute;
    top: 218px; left: 104px;
    width: 640px; height: 160px;
    background: linear-gradient(180deg, #2aa6e8, #1484c4);
    border-radius: 60px 80px 80px 60px;
  }
  .trade-band {
    position: absolute;
    top: 405px; left: 0; right: 0;
    height: 142px;
    background: var(--brand-blue);
  }
  .trade-band::before {
    content: "";
    position: absolute;
    top: 14px; left: 0; right: 0;
    height: 3px;
    background: var(--paper);
  }
  .trade-name {
    position: absolute;
    top: 26px; left: 0; right: 0;
    text-align: center;
    white-space: nowrap;
    font-family: "Arvo", Georgia, serif;
    font-weight: 700;
    font-size: 92px;
    line-height: 1.1;
    color: var(--paper);
  }
  .promise {
    position: absolute;
    top: 560px; left: 0; right: 0;
    text-align: center;
    white-space: nowrap;
    font-weight: 600;
    font-size: 30px;
  }
  .call-box {
    position: absolute;
    top: 608px; left: 38px;
    width: 755px; height: 132px;
    background: var(--brand-blue);
    border: 3px solid var(--paper);
    outline: 3px solid var(--brand-blue);
    color: var(--paper);
    text-align: center;
  }
  .call-lead { font-weight: 300; font-size: 38px; line-height: 1; margin-top: 14px; }
  .call-number { font-weight: 400; font-size: 60px; line-height: 1.15; letter-spacing: 1px; }
  .selling-points {
    position: absolute;
    top: 760px; left: 24px;
    list-style: none;
    font-weight: 800;
    font-size: 36px;
    line-height: 54px;
    color: var(--brand-blue);
  }
  .selling-points li::before { content: "• "; }
  .any-trade {
    position: absolute;
    top: 760px; left: 556px;
    white-space: nowrap;
    font-weight: 600;
    font-size: 19px;
  }
  .consultant-name {
    position: absolute;
    top: 846px; left: 540px;
    width: 270px;
    text-align: center;
    font-weight: 400;
    font-size: 28px;
    line-height: 1.15;
    color: var(--brand-blue);
  }
  .trade-list {
    position: absolute;
    top: 888px; left: 24px;
    white-space: nowrap;
    font-weight: 700;
    font-size: 15px;
    line-height: 26px;
  }
  .tear-strip {
    position: absolute;
    bottom: 0; left: 24px; right: 24px;
    height: 220px;
    display: flex;
  }
  .tab {
    position: relative;
    flex: 1 1 0;
    min-width: 0;
    border-left: 2px dashed var(--dash);
  }
  .tab:last-child { border-right: 2px dashed var(--dash); }
  .tab span {
    position: absolute;
    top: 50%; left: 50%;
    transform: translate(-50%, -50%) rotate(-90deg);
    white-space: nowrap;
    font-weight: 400;
    font-size: 21px;
  }
</style>
</head>
<body>
<main class="leaflet">
  <h1 class="headline">LOOKING FOR</h1>
  <div class="tool-art" role="img" aria-label="Illustration of a blue adjustable spanner"></div>

  <div class="trade-band">
    <h2 class="trade-name">PLUMBERS</h2>
  </div>

  <p class="promise">WE WILL HELP YOU FIND THE BEST FOR LESS</p>

  <div class="call-box">
    <p class="call-lead">JUST CALL US TODAY</p>
    <p class="call-number">01-4827316</p>
  </div>

  <ul class="selling-points">
    <li>Local Men</li>
    <li>Competitive Rates</li>
  </ul>

  <p class="any-trade">FOR ANY TRADE A – Z</p>
  <p class="consultant-name">Harlow Property Consultants</p>

  <p class="trade-list">Plumbers, Electricians, Handymen, Carpenters,<br>Plasterers, Tilers, Appliance Repairers, Cleaners Etc.</p>

  <div class="tear-strip">
    <div class="tab"><span>01-4827316</span></div>
    <div class="tab"><span>01-4827316</span></div>
    <div class="tab"><span>01-4827316</span></div>
    <div class="tab"><span>01-4827316</span></div>
    <div class="tab"><span>01-4827316</span></div>
    <div class="tab"><span>01-4827316</span></div>
    <div class="tab"><span>01-4827316</span></div>
    <div class="tab"><span>01-4827316</span></div>
    <div class="tab"><span>01-4827316</span></div>
    <div class="tab"><span>01-4827316</span></div>
    <div class="tab"><span>01-4827316</span></div>
    <div class="tab"><span>01-4827316</span></div>
  </div>
</main>
</body>
</html>
```